RWT Fittings Ltd Business Cards

We need a business card with our business logo. We provide window and door installations on high-rises in west coast British Colombia, Canada.

I would like my business information and details on one side of the card, and the other side the company name with logo

Target Market(s)

General Contractors

Industry/Entity Type

Construction

Contact Information for Business Card

one side i want my company name and logo in the dark theme logo that i provided

Requirements
Must have
• Marco Peltieri, 16045518293, RWTFittings@mailbox-demo.com, 1407-5194 Linden Row Burnaby BC, V5H 2K9, Owner & Manager

```html
<!DOCTYPE html>
<html lang="en">
<head>
<meta charset="utf-8">
<title>RWT Fittings Ltd — Business Card</title>
<link rel="stylesheet" href="https://fonts.googleapis.com/css2?family=Montserrat:wght@400;500;700&display=swap">
<style>
  :root {
    --backdrop: #232323;
    --card: #0f0f0f;
    --card-edge: #1a1a1a;
    --brand-blue: #29a8e0;
    --brand-grey: #9a9a9a;
    --text-light: #e6e6e6;
    --text-muted: #bdbdbd;
  }
  * { margin: 0; padding: 0; box-sizing: border-box; }
  html, body {
    width: 1200px; height: 900px; overflow: hidden;
    background: var(--backdrop);
    font-family: "Montserrat", sans-serif;
  }
  .canvas { position: relative; width: 1200px; height: 900px; }

  .card {
    position: absolute;
    width: 620px; height: 354px;
    border-radius: 22px;
    background: var(--card);
    border: 1px solid var(--card-edge);
    box-shadow: 0 18px 40px rgba(0,0,0,.55);
    overflow: hidden;
  }
  .card--front { left: 110px; top: 64px; }
  .card--back  { left: 470px; top: 478px; }

  /* front side */
  .wordmark {
    position: absolute;
    display: flex; align-items: center; gap: 18px;
  }
  .wordmark__square { background: var(--brand-grey); flex: none; }
  .wordmark__name {
    color: var(--brand-blue);
    font-weight: 700;
    letter-spacing: .02em;
    white-space: nowrap;
  }
  .card--front .wordmark { left: 0; right: 0; top: 0; bottom: 0; justify-content: center; }
  .card--front .wordmark__square { width: 44px; height: 44px; }
  .card--front .wordmark__name { font-size: 40px; }

  /* back side */
  .card--back .wordmark { left: 38px; top: 58px; gap: 10px; }
  .card--back .wordmark__square { width: 22px; height: 22px; }
  .card--back .wordmark__name { font-size: 21px; }

  .accent-bar {
    position: absolute; right: 26px; top: 30px;
    width: 10px; height: 40px; background: var(--brand-blue);
  }
  .person { position: absolute; right: 56px; top: 30px; text-align: right; }
  .person__name { color: var(--brand-blue); font-weight: 700; font-size: 22px; }
  .person__role { color: var(--text-light); font-size: 11px; margin-top: 2px; }

  .decor-panel {
    position: absolute; right: 40px; top: 100px;
    width: 220px; height: 210px;
    background: linear-gradient(150deg, #3a3a3a 0%, #1d1d1d 45%, #121212 100%);
    opacity: .8;
  }

  .address {
    position: absolute; left: 70px; top: 200px;
    color: var(--text-light); font-size: 13px; line-height: 1.4;
  }
  .contact-list {
    position: absolute; left: 70px; top: 252px;
    list-style: none;
    color: var(--text-light); font-size: 13px;
  }
  .contact-list li { display: flex; align-items: center; gap: 10px; height: 26px; }
  .contact-list svg { width: 15px; height: 15px; fill: var(--brand-blue); flex: none; }
</style>
</head>
<body>
<main class="canvas">

  <section class="card card--front" aria-label="Card front">
    <div class="wordmark">
      <span class="wordmark__square"></span>
      <span class="wordmark__name">RWT Fittings Ltd</span>
    </div>
  </section>

  <section class="card card--back" aria-label="Card back">
    <div class="wordmark">
      <span class="wordmark__square"></span>
      <span class="wordmark__name">RWT Fittings Ltd</span>
    </div>

    <div class="person">
      <div class="person__name">Marco Peltieri</div>
      <div class="person__role">Owner &amp; Manager</div>
    </div>
    <span class="accent-bar"></span>

    <div class="decor-panel" role="img" aria-label="Large faint brand emblem in dark glossy tones"></div>

    <p class="address">1407-5194 Linden Row<br>Burnaby BC, V5H 2K9</p>

    <ul class="contact-list">
      <li>
        <svg viewBox="0 0 16 16" aria-hidden="true"><path d="M2 6c0-2 3-3.5 6-3.5S14 4 14 6l-2.5 1L10 5.5H6L4.5 7zM4 8h8l1 6H3z"/><circle cx="8" cy="11" r="1.6" fill="#0f0f0f"/></svg>
        <span>16045518293</span>
      </li>
      <li>
        <svg viewBox="0 0 16 16" aria-hidden="true"><path d="M1 4h14v9H1z"/><path d="M1 4l7 5 7-5" fill="none" stroke="#0f0f0f" stroke-width="1.4"/></svg>
        <span>RWTFittings@mailbox-demo.com</span>
      </li>
      <li>
        <svg viewBox="0 0 16 16" aria-hidden="true"><circle cx="8" cy="8" r="7"/><path d="M1 8h14M8 1c3 3 3 11 0 14M8 1c-3 3-3 11 0 14" fill="none" stroke="#0f0f0f" stroke-width="1"/></svg>
        <span>www.rwtfittings-demo.com</span>
      </li>
    </ul>
  </section>

</main>
</body>
</html>
```